Gentle Kundalini Yoga with Gong Relaxation

I teach a gentle Kundalini Yoga class with Gong relaxation every Thursday morning from 8:30-10am at the Ashford Meadows Fellowship Church 17 Birchwell Avenue Ashford Meadows. This class is unique in that I play the gong for an extended relaxation. Gongs are generally only found in established Yoga centers not in a small neighborhood yoga class. I am trying to grow this class from a current class size of 5 students. I would like to double the class size.
Updates
Project Deadline Extended
Reason: We had a blizzard on January 27 and 28 in the Boston area and I was too busy removing snow to tend to the postcard design-Thank you-Clara Whitfield
Industry/Entity Type
Church

```html
<!DOCTYPE html>
<html lang="en">
<head>
<meta charset="utf-8">
<title>Kundalini Yoga with Gong Relaxation – Postcard</title>
<link rel="stylesheet" href="https://fonts.googleapis.com/css2?family=Roboto+Condensed:wght@400;700&display=swap">
<style>
  :root {
    --page-bg: #d9d9d9;
    --card-white: #ffffff;
    --ink: #1a1a1a;
    --ink-soft: #333333;
    --rule-grey: #9a9a9a;
    --logo-grey: #8c8c8c;
    --sun-light: #fbe3b8;
    --sun-mid: #e9a766;
    --sun-deep: #b8683a;
    --dusk: #5b3a26;
    --band-black: #0d0d0d;
    --text-light: #ffffff;
  }
  * { box-sizing: border-box; margin: 0; padding: 0; }
  html, body {
    width: 1200px;
    height: 825px;
    overflow: hidden;
    background: var(--page-bg);
    font-family: "Roboto Condensed", "Arial Narrow", sans-serif;
  }
  .sheet {
    position: relative;
    width: 1200px;
    height: 825px;
    display: flex;
    align-items: center;
    justify-content: center;
    gap: 24px;
  }
  .postcard {
    position: relative;
    width: 564px;
    height: 392px;
    overflow: hidden;
    box-shadow: 0 6px 18px rgba(0,0,0,0.25);
  }

  /* ---------- Front ---------- */
  .postcard--front { background: var(--band-black); }
  .front-photo {
    position: absolute;
    inset: 0;
    background:
      radial-gradient(circle at 18% 42%, var(--sun-light) 0%, rgba(251,227,184,0.6) 16%, rgba(233,167,102,0) 42%),
      linear-gradient(180deg, #c98a5c 0%, var(--sun-mid) 40%, var(--sun-deep) 70%, var(--dusk) 100%);
  }
  .front-hill {
    position: absolute;
    left: 0;
    bottom: 0;
    width: 100%;
    height: 170px;
  }
  .front-title {
    position: absolute;
    left: 54px;
    top: 138px;
    color: var(--ink);
    line-height: 1;
  }
  .front-title__name {
    display: block;
    font-weight: 700;
    font-size: 30px;
    letter-spacing: -0.3px;
  }
  .front-title__sub {
    display: block;
    font-weight: 700;
    font-size: 19px;
    margin-left: 42px;
    margin-top: 2px;
  }
  .front-schedule {
    position: absolute;
    right: 26px;
    bottom: 92px;
    color: var(--text-light);
    font-weight: 700;
    font-size: 19px;
    transform: rotate(-5deg);
    white-space: nowrap;
  }
  .front-schedule__day { font-size: 22px; }
  .front-phone {
    position: absolute;
    left: 30px;
    bottom: 24px;
    color: var(--text-light);
    font-weight: 700;
    font-size: 40px;
    letter-spacing: -0.5px;
  }

  /* ---------- Back ---------- */
  .postcard--back { background: var(--card-white); }
  .back-identity {
    position: absolute;
    left: 36px;
    top: 60px;
    width: 250px;
  }
  .back-mark {
    display: block;
    width: 74px;
    height: 74px;
    border-radius: 50%;
    background: var(--logo-grey);
    margin-left: 20px;
  }
  .back-title {
    margin-top: 34px;
    margin-left: 28px;
    color: var(--ink);
    line-height: 1;
  }
  .back-title__name {
    display: block;
    font-weight: 700;
    font-size: 28px;
    letter-spacing: -0.3px;
  }
  .back-title__sub {
    display: block;
    font-weight: 700;
    font-size: 17px;
    margin-left: 18px;
    margin-top: 2px;
  }
  .back-address {
    margin-top: 22px;
    margin-left: 28px;
    font-weight: 700;
    font-size: 11.5px;
    color: var(--ink-soft);
    line-height: 1.35;
  }
  .back-address__town { display: block; margin-left: 52px; }
  .back-divider {
    position: absolute;
    left: 300px;
    top: 46px;
    bottom: 40px;
    width: 1px;
    background: var(--rule-grey);
  }
  .back-stamp {
    position: absolute;
    right: 44px;
    top: 28px;
    width: 72px;
    height: 80px;
    border: 1px solid var(--rule-grey);
  }
  .back-lines {
    position: absolute;
    left: 340px;
    right: 50px;
    top: 148px;
  }
  .back-lines__line {
    height: 1px;
    border-top: 1px dotted var(--rule-grey);
    margin-bottom: 50px;
  }
</style>
</head>
<body>
<main class="sheet">

  <section class="postcard postcard--front" aria-label="Postcard front">
    <div class="front-photo" role="img" aria-label="Sunrise photo of a person in tree pose on a hilltop, with a church and trees faded into the warm sky"></div>
    <svg class="front-hill" viewBox="0 0 564 170" preserveAspectRatio="none" aria-hidden="true">
      <path d="M0 170 L0 150 C120 120 230 110 330 70 C420 35 500 20 564 8 L564 170 Z" fill="var(--band-black)"/>
    </svg>
    <h1 class="front-title">
      <span class="front-title__name">Kundalini Yoga</span>
      <span class="front-title__sub">with Gong relaxation</span>
    </h1>
    <p class="front-schedule">Every <span class="front-schedule__day">Thursday Morning</span> from 8:30-10am</p>
    <p class="front-phone">555-014-2290</p>
  </section>

  <section class="postcard postcard--back" aria-label="Postcard back">
    <div class="back-identity">
      <span class="back-mark" aria-hidden="true"></span>
      <h2 class="back-title">
        <span class="back-title__name">Kundalini Yoga</span>
        <span class="back-title__sub">with Gong relaxation</span>
      </h2>
      <p class="back-address">
        Fellowship Church 17 Birchwell Avenue
        <span class="back-address__town">Ashford Meadows</span>
      </p>
    </div>
    <div class="back-divider" aria-hidden="true"></div>
    <div class="back-stamp" aria-hidden="true"></div>
    <div class="back-lines" aria-hidden="true">
      <div class="back-lines__line"></div>
      <div class="back-lines__line"></div>
      <div class="back-lines__line"></div>
    </div>
  </section>

</main>
</body>
</html>
```